Business Card: RW Office Partners - Your organised problem solver

Business Name: RW Office Partners
Website: www.rwofficepartners.com.au
Email: marisol@rwofficepartners.com.au
Mobile: 61 482 907 236
Facebook: @rwofficepartners
Instrgram: @rwofficepartners

Brading Colours:
HEX
#986474
#ddccd3
#7a8498
#c9d8e4
#000000
#ffffff

Tag Line: Your reliable desk partner

Link to DRAFT website:
https://deskhelpcollective.wixsite.com/rw-office-partners

About Page from the website:
My name is Marisol Wrenfield, and I would love to assist you to become more productive in your day to day and achieve your business and personal goals.
My mission is to give you time, time to work on the important tasks of your business or to be able to spend more time with your family. I will take on the tasks you don’t have time for, don’t know well or simply don’t like to do.
I have an extensive background in Administration, Tender Coordination, Document Control, WHS and Quality Management working primarily in the Construction, Mining and Corporate World.
I am passionate about being organised, having order and making things in your life (and mine) easier! I love to watch something unfold and grow into something amazing! I am known for being the go-to problem solver, the organiser of all things, producing high standards of work even under pressure. I’m also a confident communicator, and I understand that you’re busy running your business.

Target Market(s)

Small to Medium Business who require assistance in their business by a virtual assistant.

Industry/Entity Type

Virtual Assistant

Contact Information for Business Card

Mobile: 61 482 907 236

Font styles to use
Sans Serif

Colors
ffffff

Requirements
Must have
• Branding Colours as outlined.
Contact Details as outlined.
Logo as provided.
Proper contact details - mobile, facebook, instragm, website.
Simple, Elegant, very clean looking.
Should not have
• Note cute with pictures.
Not too girly as still want to market to construction companies.

```html
<!DOCTYPE html>
<html lang="en">
<head>
<meta charset="utf-8">
<title>RW Office Partners – Business Card</title>
<link href="https://fonts.googleapis.com/css2?family=Montserrat:wght@600&family=Arimo:wght@400;600&family=Open+Sans:wght@400&display=swap" rel="stylesheet">
<style>
  :root {
    --plum: #986474;
    --slate: #7a8498;
    --white: #ffffff;
    --ink: #000000;
    --rule: #8a8a8a;
    --backdrop: #2e2e30;
  }
  * { margin: 0; padding: 0; box-sizing: border-box; }
  html, body { width: 1200px; height: 1200px; overflow: hidden; }
  body { background: var(--backdrop); position: relative; }

  .card {
    position: absolute;
    top: 310px;
    height: 594px;
  }
  .card--front { left: 234px; width: 364px; background: var(--white); }
  .card--back  { left: 627px; width: 369px; background: var(--slate); }

  .front__wordmark {
    position: absolute;
    top: 84px; left: 0; width: 100%;
    text-align: center;
    font-family: "Montserrat", sans-serif;
    font-weight: 600;
    font-size: 42px;
    line-height: 58px;
    letter-spacing: 1px;
    color: var(--slate);
    text-transform: uppercase;
  }

  .front__name {
    position: absolute;
    top: 337px; left: 0; width: 100%;
    text-align: center;
    font-family: "Arimo", sans-serif;
    font-weight: 600;
    font-size: 21px;
    letter-spacing: -0.3px;
    color: var(--plum);
    text-transform: uppercase;
  }

  .divider {
    position: absolute;
    left: 0; width: 100%;
    display: flex; justify-content: center; align-items: center;
  }
  .divider__line { width: 50px; height: 1px; background: var(--rule); }
  .divider__line--wide { width: 60px; }
  .divider__icons { display: flex; gap: 6px; margin: 0 6px; }
  .divider--contact { top: 383px; }
  .divider--social  { top: 496px; }

  .icon-tile {
    width: 24px; height: 24px; border-radius: 3px;
    background: var(--plum);
    display: flex; align-items: center; justify-content: center;
  }
  .social-dot {
    width: 25px; height: 25px; border-radius: 50%;
    border: 1.2px solid var(--slate);
  }

  .front__contacts {
    position: absolute;
    top: 418px; left: 0; width: 100%;
    text-align: center;
    font-family: "Arimo", sans-serif;
    font-size: 17px;
    line-height: 22px;
    color: var(--ink);
  }
  .front__handle {
    position: absolute;
    top: 529px; left: 0; width: 100%;
    text-align: center;
    font-family: "Arimo", sans-serif;
    font-size: 17px;
    color: var(--ink);
  }

  .back__wordmark {
    position: absolute;
    left: 56px; top: 410px;
    font-family: "Montserrat", sans-serif;
    font-weight: 600;
    font-size: 40px;
    line-height: 46px;
    letter-spacing: 1px;
    color: var(--white);
    text-transform: uppercase;
  }
  .back__tagline {
    position: absolute;
    left: 52px; top: 526px;
    font-family: "Open Sans", sans-serif;
    font-size: 15px;
    color: var(--white);
    text-transform: uppercase;
  }
</style>
</head>
<body>
  <section class="card card--front" aria-label="Business card front">
    <div class="front__wordmark">RW<br>Office<br>Partners</div>
    <div class="front__name">Marisol Wrenfield</div>

    <div class="divider divider--contact">
      <span class="divider__line"></span>
      <div class="divider__icons">
        <span class="icon-tile" aria-label="Phone">
          <svg width="14" height="14" viewBox="0 0 24 24"><path fill="#fff" d="M6.6 10.8c1.4 2.8 3.8 5.1 6.6 6.6l2.2-2.2c.3-.3.7-.4 1-.2 1.1.4 2.3.6 3.6.6.6 0 1 .4 1 1V20c0 .6-.4 1-1 1C10.6 21 3 13.4 3 4c0-.6.4-1 1-1h3.5c.6 0 1 .4 1 1 0 1.3.2 2.5.6 3.6.1.3 0 .7-.2 1z"/></svg>
        </span>
        <span class="icon-tile" aria-label="Email">
          <svg width="14" height="14" viewBox="0 0 24 24"><rect x="2" y="5" width="20" height="14" fill="none" stroke="#fff" stroke-width="2"/><path d="M2 5l10 8 10-8" fill="none" stroke="#fff" stroke-width="2"/></svg>
        </span>
        <span class="icon-tile" aria-label="Website">
          <svg width="14" height="14" viewBox="0 0 24 24"><circle cx="12" cy="12" r="9" fill="none" stroke="#fff" stroke-width="2"/><path d="M3 12h18M12 3c3 3 3 15 0 18M12 3c-3 3-3 15 0 18" fill="none" stroke="#fff" stroke-width="1.6"/></svg>
        </span>
      </div>
      <span class="divider__line"></span>
    </div>

    <div class="front__contacts">
      61 482 907 236<br>
      marisol@rwofficepartners.com.au<br>
      www.rwofficepartners.com.au
    </div>

    <div class="divider divider--social">
      <span class="divider__line divider__line--wide"></span>
      <div class="divider__icons">
        <span class="social-dot" aria-label="Social profile"></span>
        <span class="social-dot" aria-label="Social profile"></span>
      </div>
      <span class="divider__line divider__line--wide"></span>
    </div>

    <div class="front__handle">@rwofficepartners</div>
  </section>

  <section class="card card--back" aria-label="Business card back">
    <div class="back__wordmark">RW Office<br>Partners</div>
    <div class="back__tagline">Your reliable desk partner</div>
  </section>
</body>
</html>
```